Wellbeing Challenge Posters

We are running a wellbeing challenge. Every week we run a challenge under a different theme. We need 5 themes to start with:
- Connect
- Be mindful
- Get moving
- Give
- Grow your mind

Each theme needs to have the following:
1. Match the colours of the icons provided under each
2. Have a clear place for the word where these can be changed but utilising the same theme. For example, under connect, we will run a number of different challenges but the theme will remain the same.
3. Each theme will have the following:
-This week's challenge
- Points
4. The Flourish Challenge logo

The content under each of the themes will be as follows:

1. Connect
This week's challenge: Have a shared meal with your team - take a photo and post it on the challenge forum
Points: 10 points per person that attended if you had more than 75% of your team

2. Be Mindful
This week's challenge: START something that will improve your wellbeing, STOP something that is bad for you - Be mindful of how you feel at the end of the week.

3. Get moving:
This week's challenge: Do a minimum 150 minutes of exercise this week required for good general health - try something new!
Points: Take your usual 1 point per 30 mins exercise but give yourself an additional 10 points if you do 150mins or more for the week.

4. Give:
This week's challenge: Do a random act of kindness every day this week
Points: 1 point per day PLUS 10 points if you complete 1 every day

5. Grow Your Mind
This week's challenge: Learn something new every day! Read a research paper, watch a BIX talk, DIY, learn something about your workmates

```html
<!DOCTYPE html>
<html lang="en">
<head>
<meta charset="utf-8">
<title>Connect – This Week's Challenge</title>
<link rel="stylesheet" href="https://fonts.googleapis.com/css2?family=Montserrat:wght@800&family=Patrick+Hand&display=swap">
<style>
  :root {
    --teal: #1fbcb5;
    --teal-dark: #05766f;
    --teal-ring: #0b5c57;
    --badge-teal: #1aa6b6;
    --brand-grey: #6d6e71;
    --ink: #111111;
    --white: #ffffff;
  }
  html, body {
    margin: 0;
    padding: 0;
    overflow: hidden;
    background: var(--white);
  }
  .poster {
    position: relative;
    width: 917px;
    height: 1200px;
    overflow: hidden;
    background: var(--white);
  }
  .brand {
    position: absolute;
    left: 0;
    top: 100px;
    width: 917px;
    margin: 0;
    text-align: center;
    font-family: "Montserrat", sans-serif;
    font-weight: 800;
    font-size: 34px;
    line-height: 1;
    color: var(--brand-grey);
  }
  .theme-band {
    position: absolute;
    left: 0;
    top: 0;
  }
  .theme-title {
    position: absolute;
    left: 300px;
    top: 318px;
    margin: 0;
    font-family: "Montserrat", sans-serif;
    font-weight: 800;
    font-size: 50px;
    letter-spacing: -2px;
    color: var(--white);
  }
  .challenge-heading {
    position: absolute;
    left: 288px;
    top: 462px;
    margin: 0;
    font-family: "Patrick Hand", cursive;
    font-size: 44px;
    font-weight: 400;
    color: var(--ink);
  }
  .challenge-text {
    position: absolute;
    left: 192px;
    top: 520px;
    width: 690px;
    margin: 0;
    font-family: "Patrick Hand", cursive;
    font-size: 30px;
    line-height: 41px;
    color: var(--ink);
  }
  .points-heading {
    position: absolute;
    left: 13px;
    top: 617px;
    margin: 0;
    font-family: "Patrick Hand", cursive;
    font-size: 46px;
    font-weight: 400;
    color: var(--ink);
  }
  .points-text {
    position: absolute;
    left: 13px;
    top: 669px;
    margin: 0;
    font-family: "Patrick Hand", cursive;
    font-size: 30.5px;
    color: var(--ink);
    white-space: nowrap;
  }
</style>
</head>
<body>
<main class="poster">
  <header>
    <p class="brand">The Flourish Challenge</p>
  </header>

  <svg class="theme-band" width="917" height="1200" viewBox="0 0 917 1200" aria-hidden="true">
    <rect x="0" y="247" width="917" height="19" fill="var(--teal-dark)"/>
    <polygon points="0,266 917,266 917,440 297,440 0,593" fill="var(--teal)"/>
    <polygon points="0,600 300,446 917,446 917,454 302,454 0,610" fill="var(--teal)"/>
    <rect x="0" y="348" width="100" height="16" fill="var(--teal-ring)"/>
    <circle cx="164" cy="391" r="74" fill="var(--white)" stroke="var(--teal-ring)" stroke-width="7"/>
    <circle cx="164" cy="392" r="37" fill="var(--badge-teal)"/>
  </svg>

  <h1 class="theme-title">CONNECT</h1>

  <section class="challenge">
    <h2 class="challenge-heading">This week’s challenge</h2>
    <p class="challenge-text">Have a shared meal with your team - take a photo and post it on the challenge forum.</p>
  </section>

  <section class="points">
    <h2 class="points-heading">Points</h2>
    <p class="points-text">10 points per person that attended if you had more than 75% of your team.</p>
  </section>
</main>
</body>
</html>
```